Social Media Graphics - Oakline Push REVISED

Create 6-7 individual social media graphics (square size) to encourage folks to join our online course called:

The Harvest Ledger Circle
How to Launch a Multi-Million Business From Scratch
Sign Up Today!

IMPORTANT: Make the largest and most prominent text on the graphic be: How to Launch a Multi-Million Business From Scratch

For the color scheme of the graphics, let's try a blue color palette; make sure the graphics appeal to both men and women

Make sure each graphic contains 1 of the 3 pics attached (crop pic as needed); and make sure one of the graphics is all TEXT only.

Target Market(s)

men and women looking to start a business

Industry/Entity Type

Entrepreneurship

Colors
0054AA
0677BA
7BADD7
CADEEF
E8F1F8

Requirements
Must have
• All the text and use the 3 pics provided; one graphic can be all text; Simple, modern design that's easy to read

```html
<!DOCTYPE html>
<html lang="en">
<head>
<meta charset="UTF-8">
<title>The Harvest Ledger Circle — Social Graphic</title>
<link rel="stylesheet" href="https://fonts.googleapis.com/css2?family=Bebas+Neue&display=swap">
<style>
  :root {
    --sky-top: #0a8fd6;
    --sky-mid: #0677ba;
    --sky-bottom: #003e72;
    --ink-panel: #161d30;
    --panel-shadow: #246a9c;
    --white: #ffffff;
    --photo-dark: #1b2230;
    --photo-skin: #6b4a3a;
    --photo-denim: #1f4f8a;
  }
  * { margin: 0; padding: 0; box-sizing: border-box; }
  html, body {
    width: 1200px; height: 1200px; overflow: hidden;
    background: var(--sky-bottom);
  }
  .graphic {
    position: relative;
    width: 1200px; height: 1200px; overflow: hidden;
    background: radial-gradient(ellipse 90% 70% at 50% 18%, var(--sky-top) 0%, var(--sky-mid) 40%, var(--sky-bottom) 100%);
    font-family: "Bebas Neue", "Oswald", sans-serif;
    color: var(--white);
  }
  .host-photo {
    position: absolute;
    border-radius: 140px 140px 0 0;
  }
  .host-photo--left {
    left: 99px; top: 65px; width: 360px; height: 555px;
    background: linear-gradient(180deg, var(--photo-skin) 0%, var(--photo-dark) 32%, var(--photo-dark) 100%);
  }
  .host-photo--right {
    left: 732px; top: 93px; width: 386px; height: 527px;
    background: linear-gradient(180deg, #2a1c18 0%, var(--photo-skin) 18%, var(--photo-denim) 38%, #173f70 100%);
  }
  .title-stack {
    position: absolute;
    left: 470px; width: 260px; top: 150px;
    text-align: center;
    font-weight: 400;
    line-height: 0.92;
  }
  .title-stack__small { display: block; font-size: 100px; letter-spacing: 6px; }
  .title-stack__large { display: block; font-size: 90px; letter-spacing: 1px; }
  .title-panel-shadow {
    position: absolute;
    left: 99px; top: 620px; width: 1010px; height: 150px;
    background: var(--panel-shadow);
    border-radius: 20px;
  }
  .title-panel {
    position: absolute;
    left: 92px; top: 628px; width: 1001px; height: 150px;
    background: var(--ink-panel);
    border-radius: 24px;
    display: flex; align-items: center; justify-content: center;
  }
  .title-panel__word {
    font-size: 100px; line-height: 1;
    letter-spacing: 22px;
    padding-left: 22px;
    padding-top: 8px;
  }
  .headline {
    position: absolute;
    left: 0; width: 1200px; top: 806px;
    text-align: center;
    font-weight: 400;
    font-size: 104px; line-height: 112px;
    letter-spacing: 1px;
  }
  .cta-divider {
    position: absolute;
    left: 163px; width: 887px; top: 1052px;
    display: flex; align-items: center; gap: 18px;
  }
  .cta-divider__rule { flex: 1; height: 2px; background: var(--white); }
  .cta-divider__label { font-size: 30px; letter-spacing: 12px; padding-left: 12px; line-height: 1; }
  .signup-button {
    position: absolute;
    left: 440px; top: 1098px; width: 345px; height: 37px;
    background: var(--ink-panel);
    display: flex; align-items: center; justify-content: center;
    font-size: 30px; letter-spacing: 11px; line-height: 1;
    padding-top: 3px; padding-left: 11px;
  }
</style>
</head>
<body>
  <main class="graphic">
    <div class="host-photo host-photo--left" role="img" aria-label="Photo of male course host in a black turtleneck, arms crossed"></div>
    <div class="host-photo host-photo--right" role="img" aria-label="Photo of female course host in a blue denim jacket"></div>

    <h1 class="title-stack">
      <span class="title-stack__small">The</span>
      <span class="title-stack__large">Harvest</span>
      <span class="title-stack__large">Ledger</span>
    </h1>

    <div class="title-panel-shadow"></div>
    <div class="title-panel"><span class="title-panel__word">CIRCLE</span></div>

    <h2 class="headline">How to Launch a Multi-Million<br>Business From Scratch</h2>

    <div class="cta-divider">
      <span class="cta-divider__rule"></span>
      <span class="cta-divider__label">CTA</span>
      <span class="cta-divider__rule"></span>
    </div>

    <div class="signup-button">Sign Up Today</div>
  </main>
</body>
</html>
```